"LuvaWorks" Graphic Design Project

We are a new business creating bath/ body/beauty products. We need label designs for men "Velto for Men " and women- "Velto for Women" . Since the collection called Velto will be used for both- we'd like the labels to look similar but separating the gender look- maybe by a same color variation. Our bottles are amber in color , so we like the beiges, cream, and earthy warm tones - greens- brown-orange- yellow-colors. The labels are for 8 oz amber cosmo round bottles. The height is 7.32inches and the diameter is 1.85 inches.
Our starting line will be Velto for Men ( Silk Body Wash, Silk Body Lotion and Body Mist) and the same for Velto for Women.

Target Market(s)

Our target audience is between 30 to 60 years of age. Salons and private consumers.
I am including attached sample of what was started by me.

Requirements
Must have
• We would like to incorporate the company name- LuvaWorks along with the name of the product- which will be Velto for Men or Velto for Women on each label.

On label with company name or somewhere on label we would like a tree to symbolize the beginning, but we are open to suggestions.

```html
<!DOCTYPE html>
<html lang="en">
<head>
<meta charset="utf-8">
<title>Velto for Men – Silk Body Wash Label</title>
<link rel="stylesheet" href="https://fonts.googleapis.com/css2?family=Quicksand:wght@500&family=Didact+Gothic&display=swap">
<style>
  :root {
    --ink: #1f1a16;
    --brown: #8a6446;
    --tan: #9a7458;
    --panel: rgba(255, 252, 249, 0.78);
  }
  html, body {
    margin: 0;
    padding: 0;
    width: 954px;
    height: 1200px;
    overflow: hidden;
    background: #ffffff;
  }
  .label {
    position: relative;
    width: 954px;
    height: 1200px;
    overflow: hidden;
    font-family: "Didact Gothic", sans-serif;
    color: var(--ink);
  }
  .label__backdrop {
    position: absolute;
    inset: 0;
    background:
      radial-gradient(ellipse 260px 200px at 250px 110px, rgba(206,160,118,0.75), transparent 70%),
      radial-gradient(ellipse 300px 240px at 300px 620px, rgba(201,148,140,0.55), transparent 70%),
      radial-gradient(ellipse 300px 260px at 820px 470px, rgba(236,196,186,0.7), transparent 70%),
      radial-gradient(ellipse 240px 220px at 860px 980px, rgba(226,180,176,0.6), transparent 70%),
      radial-gradient(ellipse 320px 260px at 420px 940px, rgba(240,222,196,0.9), transparent 70%),
      linear-gradient(160deg, #efd8bf 0%, #f3e3d2 35%, #ecd2c3 60%, #f3e2cf 100%);
  }
  .label__band {
    position: absolute;
    left: 0;
    top: 0;
    width: 98px;
    height: 1200px;
    background: linear-gradient(90deg, rgba(255,250,244,0.85), rgba(250,240,230,0.7));
  }
  .company-name {
    position: absolute;
    left: 49px;
    top: 599px;
    transform: translate(-50%, -50%) rotate(-90deg);
    font-family: "Didact Gothic", sans-serif;
    font-weight: 400;
    font-size: 58px;
    line-height: 1;
    letter-spacing: 4px;
    color: var(--brown);
    white-space: nowrap;
  }
  .product-name {
    position: absolute;
    left: 128px;
    top: 194px;
    margin: 0;
    font-family: "Quicksand", sans-serif;
    font-weight: 500;
    font-size: 90px;
    line-height: 1;
    color: var(--brown);
  }
  .product-line {
    position: absolute;
    right: 585px;
    top: 290px;
    font-size: 29px;
    line-height: 32px;
    color: var(--tan);
  }
  .product-type {
    position: absolute;
    left: 156px;
    top: 612px;
    font-size: 33px;
    line-height: 38px;
    color: var(--brown);
  }
  .copy {
    position: absolute;
    left: 428px;
    width: 540px;
    text-align: center;
    font-size: 24.5px;
    line-height: 32.5px;
    margin: 0;
    white-space: nowrap;
  }
  .copy--intro { top: 96px; }
  .copy--directions { top: 225px; }
  .copy--warnings { top: 322px; }
  .copy--claim { top: 421px; }
  .ingredients {
    position: absolute;
    left: 440px;
    top: 555px;
    width: 485px;
    height: 417px;
    border-radius: 22px;
    background: var(--panel);
  }
  .ingredients__text {
    position: absolute;
    left: 0;
    right: 0;
    top: 34px;
    margin: 0;
    text-align: center;
    font-size: 19.5px;
    line-height: 27.2px;
  }
  .ingredients__text span { display: block; white-space: nowrap; }
  .origin {
    position: absolute;
    left: 190px;
    width: 200px;
    top: 1108px;
    text-align: center;
    font-size: 23px;
    line-height: 36px;
    color: var(--tan);
    white-space: nowrap;
  }
  .maker {
    position: absolute;
    left: 444px;
    width: 508px;
    top: 1057px;
    text-align: center;
    font-size: 23px;
    line-height: 32.5px;
    color: var(--ink);
    opacity: 0.85;
    white-space: nowrap;
  }
</style>
</head>
<body>
<main class="label">
  <div class="label__backdrop" role="img" aria-label="Soft blurred beige, cream and blush background with faint swirl ornaments"></div>
  <div class="label__band"></div>
  <div class="company-name">LuvaWorks</div>

  <h1 class="product-name">Velto</h1>
  <div class="product-line">FOR MEN</div>
  <div class="product-type">Silk Body Wash</div>

  <p class="copy copy--intro">Our Nourishing Silk Body Wash will engulf you<br>in luxurious lather as it gently cleanses your<br>delicate skin leaving it soft as silk.</p>
  <p class="copy copy--directions">Directions: Apply to skin while damp with<br>sponge or wash cloth. Rinse well.</p>
  <p class="copy copy--warnings">WARNINGS/CAUTIONS: For external use only.<br>Avoid contact with eyes.</p>
  <p class="copy copy--claim">NOT TESTED ON ANIMALS</p>

  <section class="ingredients">
    <p class="ingredients__text">
      <span>INGREDIENTS: purified water, sodium olefin</span>
      <span>sulfonate (plant source), organic aloe barbadensis</span>
      <span>leaf juice, cocamidopropyl betaine (plant source),</span>
      <span>sodium chloride (salt), kosher vegetable glycerin,</span>
      <span>tocopherol (natural vitamin E), polysorbate 20</span>
      <span>(plant source), potassium sorbate (plant source),</span>
      <span>phenoxyethanol (mild preservative), caprylyl glycol</span>
      <span>(plant source), organic anthemis nobilis (chamo-</span>
      <span>mile) extract, organic calendula officinalis flower</span>
      <span>extract, xanthan gum (plant source), magnesium</span>
      <span>ascorbyl phosphate (vitamin C ester), sodium</span>
      <span>bicarbonate (baking soda), citric acid fragrance.</span>
    </p>
  </section>

  <div class="origin">MADE IN USA<br>8.25 fl oz. / 244mL</div>
  <div class="maker">Luvaworks<br>Bath – Body - Home<br>Tampa, FL&nbsp; 33601<br>Shop 24/7 - www.luvaworks.com</div>
</main>
</body>
</html>
```